Business card for medical clinic

I need an upmarket, modern medical/health business card for my clinic

Contact Information for Business Card

name, address, email, qr code

```html
<!DOCTYPE html>
<html lang="en">
<head>
<meta charset="utf-8">
<title>Calder Health Partners – Business Card</title>
<link rel="stylesheet" href="https://fonts.googleapis.com/css2?family=Poppins:wght@300;400;500;700&display=swap">
<style>
  :root {
    --stage: #232325;
    --card: #1f1f22;
    --card-pattern-a: #26262a;
    --card-pattern-b: #1b1b1e;
    --accent: #1e9ad6;
    --ink: #ffffff;
    --muted: #9aa3ab;
  }
  * { box-sizing: border-box; margin: 0; padding: 0; }
  html, body { width: 1200px; height: 711px; overflow: hidden; }
  body {
    background: var(--stage);
    font-family: "Poppins", sans-serif;
    color: var(--ink);
    position: relative;
  }
  .card {
    position: absolute;
    top: 206px;
    width: 525px;
    height: 300px;
    background: var(--card);
    border-radius: 22px;
    border: 3px solid var(--accent);
    overflow: hidden;
  }
  .card--back { left: 45px; }
  .card--front { left: 630px; }

  /* Back */
  .back-pattern {
    position: absolute; inset: 0;
    background: radial-gradient(ellipse at 70% 10%, var(--card-pattern-a), var(--card-pattern-b) 75%);
  }
  .back-brand {
    position: absolute; right: 60px; top: 128px;
    display: flex; align-items: center; gap: 7px;
    font-size: 10px; font-weight: 500; letter-spacing: 1.5px;
    color: var(--accent); text-transform: uppercase;
  }
  .brand-dot {
    width: 14px; height: 14px; border-radius: 50%;
    border: 2px solid var(--accent);
  }

  /* Front */
  .front-brand {
    position: absolute; left: 34px; top: 124px;
    display: flex; align-items: center; gap: 12px;
    font-size: 19px; font-weight: 500; letter-spacing: 2px;
    color: var(--accent); text-transform: uppercase; line-height: 1.15;
  }
  .front-brand .brand-dot { width: 46px; height: 46px; border-width: 3px; flex: none; }
  .divider {
    position: absolute; left: 262px; top: 52px;
    width: 1px; height: 196px; background: var(--accent);
  }
  .details { position: absolute; left: 290px; top: 56px; }
  .person-name { font-size: 27px; color: var(--accent); line-height: 1; }
  .person-name .first { font-weight: 700; }
  .person-name .last { font-weight: 300; }
  .person-role { font-size: 12px; font-weight: 500; margin-top: 4px; }
  .address {
    font-size: 12px; color: var(--accent); margin-top: 16px; line-height: 1.45;
    font-style: normal;
  }
  .contacts { list-style: none; margin-top: 16px; }
  .contacts li {
    display: flex; align-items: center; gap: 9px;
    font-size: 12.5px; line-height: 1; margin-bottom: 9px;
  }
  .contacts svg { width: 13px; height: 13px; flex: none; }
</style>
</head>
<body>
  <section class="card card--back" aria-label="Card back">
    <div class="back-pattern" role="img" aria-label="Embossed repeating brand symbol pattern in dark grey"></div>
    <div class="back-brand"><span class="brand-dot"></span>Calder Health</div>
  </section>

  <section class="card card--front" aria-label="Card front">
    <div class="front-brand"><span class="brand-dot"></span><span>Calder<br>Health</span></div>
    <div class="divider"></div>
    <div class="details">
      <h1 class="person-name"><span class="first">Maren</span> <span class="last">Solvik</span></h1>
      <p class="person-role">Founder &amp; CEO</p>
      <address class="address">418 Linden Ave. Suite 300<br>Riverton, TX 75210</address>
      <ul class="contacts">
        <li>
          <svg viewBox="0 0 24 24" fill="var(--accent)"><path d="M6.6 10.8a15 15 0 0 0 6.6 6.6l2.2-2.2c.3-.3.7-.4 1-.2 1.1.4 2.3.6 3.6.6.6 0 1 .4 1 1V20c0 .6-.4 1-1 1A17 17 0 0 1 3 4c0-.6.4-1 1-1h3.5c.6 0 1 .4 1 1 0 1.3.2 2.5.6 3.6.1.3 0 .7-.2 1z"/></svg>
          (555) 214-6630
        </li>
        <li>
          <svg viewBox="0 0 24 24" fill="none" stroke="var(--accent)" stroke-width="2"><rect x="3" y="5" width="18" height="14" rx="1"/><path d="M3 6l9 7 9-7"/></svg>
          hello@calderhealth.com
        </li>
        <li>
          <svg viewBox="0 0 24 24" fill="none" stroke="var(--accent)" stroke-width="2"><circle cx="12" cy="12" r="9"/><path d="M3 12h18M12 3c3 3 3 15 0 18M12 3c-3 3-3 15 0 18"/></svg>
          www.calderhealth.com
        </li>
      </ul>
    </div>
  </section>
</body>
</html>
```